Black Car Limousine transportation business in Naples Florida

Always stand for my reliability and RVD stands for Love, K and M are the first initials of my children's names. It should show professionalism and a dedication to customer service. We keep our clients identities private. Show our professionalism. We are Black car Black tie company. We service transportation on a reserve basis to and from residents, airports, casinos, hotels,

Target Market(s)

It is a Private car service. High end clients. Businesses, Celebrity and athletes. Service to airports, hotels, special events.

Industry/Entity Type

Business

Contact Information for Business Card

A pearl metallic or Luster card. Standard business card size. Would like the name, Company email, show we take credit cards and phone number. Currently I don't have a website but will like to add later.

Logo Text

STEADFAST RVD TRANSPORTATION

Font styles to use
Serif

Colors
eaeaea
000000

Requirements
Must have
• Must have Company email, show we take credit cards and phone number. Currently I don't have a website but will like to add later.
Nice to have
• Would like to stay with a black and white theme. Open to some color trim.
Should not have
• Open to suggestions

```html
<!DOCTYPE html>
<html lang="en">
<head>
<meta charset="utf-8">
<title>Steadfast RVD Transportation – Business Card</title>
<link rel="stylesheet" href="https://fonts.googleapis.com/css2?family=Lora:wght@400;600;700&display=swap">
<style>
  :root {
    --stage-top: #2a2a2a;
    --stage-bottom: #050505;
    --card-white: #ffffff;
    --ink: #1e1e1e;
    --ink-soft: #333333;
    --band: #3a3a3a;
    --back-face: #4a4a4a;
    --text-light: #ffffff;
    --vehicle-dark: #151515;
    --vehicle-mid: #3c3c3c;
  }
  * { margin: 0; padding: 0; box-sizing: border-box; }
  html, body { width: 1200px; height: 900px; overflow: hidden; }
  body {
    position: relative;
    background: linear-gradient(180deg, var(--stage-top) 0%, var(--stage-bottom) 100%);
    font-family: "Lora", Georgia, serif;
    color: var(--ink);
  }
  .card {
    position: absolute;
    top: 306px;
    width: 439px;
    height: 271px;
    border-radius: 10px;
    overflow: hidden;
  }
  .card-front { left: 149px; background: var(--card-white); }
  .card-back { left: 609px; background: var(--back-face); }

  .wordmark {
    position: absolute;
    font-weight: 700;
    line-height: 1.1;
  }
  .wordmark span { display: block; }
  .card-front .wordmark {
    left: 41px; top: 84px;
    font-size: 17px;
    letter-spacing: 0.01em;
    color: var(--ink);
  }
  .card-back .wordmark {
    left: 0; right: 0; top: 92px;
    text-align: center;
    font-size: 30px;
    letter-spacing: 0.01em;
    color: var(--text-light);
  }

  .holder { position: absolute; left: 232px; top: 48px; }
  .holder-name { font-size: 18px; font-weight: 600; color: var(--ink); line-height: 1.15; }
  .holder-title { font-size: 11.5px; color: var(--ink-soft); margin-left: 3px; line-height: 1.3; }

  .contact-list {
    position: absolute; left: 232px; top: 96px;
    list-style: none;
    font-size: 11.5px;
    color: var(--ink);
  }
  .contact-list li { display: flex; align-items: center; height: 16px; white-space: nowrap; }
  .contact-list svg { width: 9px; height: 9px; margin-right: 5px; flex: none; }

  .address-band {
    position: absolute; left: 0; right: 0; bottom: 0; height: 59px;
    background: var(--band);
  }
  .address {
    position: absolute; left: 42px; top: 12px;
    font-size: 11.5px; line-height: 15px;
    color: var(--text-light);
    font-style: normal;
  }
  .vehicle-photo {
    position: absolute; left: 249px; top: 172px;
    width: 181px; height: 97px;
    border-radius: 14px 20px 6px 6px;
    background: linear-gradient(180deg, var(--vehicle-mid) 0%, var(--vehicle-dark) 70%);
  }
</style>
</head>
<body>
  <section class="card card-front" aria-label="Card front">
    <div class="wordmark"><span>STEADFAST RVD</span><span>TRANSPORTATION</span></div>

    <div class="holder">
      <div class="holder-name">Daniel Brooks</div>
      <div class="holder-title">Managing Director</div>
    </div>

    <ul class="contact-list">
      <li><svg viewBox="0 0 10 10"><path fill="#1e1e1e" d="M1 3c0-1 1-2 4-2s4 1 4 2v1H7V3H3v1H1z M2 5h6l1 4H1z"/></svg>555-010-2040</li>
      <li><svg viewBox="0 0 10 10"><path fill="#1e1e1e" d="M0 2h10v6H0z"/><path d="M0 2l5 3 5-3" fill="none" stroke="#fff" stroke-width="0.8"/></svg>hello@steadfastrvd.com</li>
      <li><svg viewBox="0 0 10 10"><path d="M4 6l2-2M3 5L1.5 6.5a1.5 1.5 0 0 0 2 2L5 7M7 5l1.5-1.5a1.5 1.5 0 0 0-2-2L5 3" fill="none" stroke="#1e1e1e" stroke-width="1.2"/></svg>www.steadfastrvd.com</li>
      <li><svg viewBox="0 0 10 10"><rect x="0" y="1.5" width="10" height="7" rx="1" fill="#1e1e1e"/><rect x="0" y="3" width="10" height="1.4" fill="#fff"/></svg>Major credit cards accepted</li>
    </ul>

    <div class="address-band">
      <address class="address">5678, Harbor View Lane<br>Naples, FL 34102</address>
    </div>

    <div class="vehicle-photo" role="img" aria-label="Photo of a black luxury SUV"></div>
  </section>

  <section class="card card-back" aria-label="Card back">
    <div class="wordmark"><span>STEADFAST RVD</span><span>TRANSPORTATION</span></div>
  </section>
</body>
</html>
```